Harbor Crest Holdings Corporate Showcase

Provide an attractive Corporate Website for a boutique Investment Company to showcase our activities and corporate interests.

Our Company works across a number of Sectors including

Real Estate
E-Commerce
Healthcare
Beauty & Personal Care
Technology
Resources

Lets keep the personality

Modern
Global
Sophisticated
Calm
Interesting

Lets keep the pages with MINIMAL Words
Lets use Photos/ Imagery to tell the story

We'll need a Banner Menu -
About Us
Expertise
Global Outlook
Sectors
Management
Media
Contact Us

Many thanks
Best wishes
Dennis.

Target Market(s)

Investors
Clients

Coding

Coded - Design and coding required

Number of Pages Required

5+ page

Font styles to use
Sans Serif

Colors
886aae
3176b5
00a990
f68e4d
f04a50
e667a6

Requirements
Must have
• WordPress Coding

Checkout this Website for look and feel - its cool:
www.qvr-example.com

Harbor Crest Partners
(Harbor Crest Holdings LLP)
London
E9 4ZX
United Kingdom

www.HarborCrestPartners-example.com
Nice to have
• Sophisticated colour palette - black/ brown/ blue/ purple/

```html
<!DOCTYPE html>
<html lang="en">
<head>
<meta charset="utf-8">
<title>Harbor Crest Partners</title>
<link href="https://fonts.googleapis.com/css2?family=Libre+Franklin:wght@300;400;500;600;700&display=swap" rel="stylesheet">
<style>
:root{
  --red:#f04a50;
  --ink:#1e1e1e;
  --text:#333;
  --muted:#888;
  --band:#f2f2f7;
  --footer:#23233b;
  --white:#fff;
}
*{margin:0;padding:0;box-sizing:border-box}
html,body{width:1200px;height:4467px;overflow:hidden}
body{font-family:"Libre Franklin",Arial,sans-serif;color:var(--text);background:var(--white);position:relative}
.abs{position:absolute}
.eyebrow{font-size:12px;letter-spacing:2px;color:var(--red);font-weight:600;text-transform:uppercase}
.h2{font-size:31px;font-weight:300;color:var(--ink)}
.center{left:0;width:1200px;text-align:center}
.para{font-size:12.5px;line-height:24px;color:var(--muted);font-weight:300}
.btn-dark{background:var(--ink);color:#fff;font-size:11.5px;letter-spacing:3px;font-weight:600;display:flex;align-items:center;justify-content:center;text-transform:uppercase}
.btn-line{border:1.5px solid #555;color:var(--ink);font-size:10.5px;letter-spacing:3px;font-weight:600;display:flex;align-items:center;justify-content:center;text-transform:uppercase;background:#fff}
.photo{display:block}

/* hero */
.hero{left:0;top:0;width:1200px;height:637px;background:linear-gradient(100deg,#2b2f36 0%,#4a4e55 40%,#6e6458 60%,#3a3c40 100%)}
.hero-shade{left:0;top:0;width:1200px;height:637px;background:linear-gradient(90deg,rgba(0,0,0,.35),rgba(0,0,0,0) 60%)}
.brand{left:92px;top:36px;font-size:23px;font-weight:300;color:#fff}
.nav{left:430px;top:44px;display:flex;gap:28px;font-size:11.5px;color:#fff}
.nav .active{position:relative}
.nav .active:before,.nav .active:after{content:"";position:absolute;left:0;right:0;height:1.5px;background:var(--red)}
.nav .active:before{top:-9px}.nav .active:after{bottom:-10px}
.social{display:flex;gap:14px}
.social span{width:9px;height:9px;border-radius:50%;background:#fff;display:block}
.hero-sub{left:94px;top:265px;font-size:27px;font-weight:300;color:#fff}
.hero-title{left:94px;top:298px;font-size:44px;font-weight:300;color:#fff}
.hero-btn{left:94px;top:376px;width:157px;height:39px;background:var(--red);color:#fff;font-size:11.5px;letter-spacing:3px;font-weight:600;display:flex;align-items:center;justify-content:center}
.dots{left:94px;top:575px;display:flex;gap:26px;align-items:center;font-size:13px;color:#fff}
.dots .on{width:31px;height:31px;border-radius:50%;background:var(--red);display:flex;align-items:center;justify-content:center}

/* about */
.frame{border-color:var(--red);border-style:solid}

/* sectors */
.band{left:0;width:1200px;background:var(--band)}
.card-title{font-size:16px;color:var(--ink);font-weight:400}
.arrow{width:57px;height:57px;display:flex;align-items:center;justify-content:center}

/* blog */
.meta{font-size:10px;color:var(--red);font-weight:600}
.meta b{color:var(--muted);font-weight:500}
.post-title{font-size:24px;font-weight:300;color:var(--ink)}

/* team */
.bracket{height:18px;border:2px solid var(--red);border-bottom:none}
.member-name{font-size:16px;color:var(--ink);text-align:center}
.member-role{font-size:9.5px;color:#555;font-style:normal;letter-spacing:1px;text-align:center}
.member-text{font-size:12px;line-height:18px;color:var(--muted);text-align:center;font-weight:300}

/* contact */
.contact-card{left:149px;top:3702px;width:957px;height:338px;background:#fff;box-shadow:0 4px 18px rgba(0,0,0,.08)}
.contact-box{left:94px;top:3728px;width:306px;height:293px;background:var(--red);color:#fff}
.field-label{font-size:12px;color:#888}
.field-line{height:1px;background:#999}

/* footer */
.footer{left:0;top:4097px;width:1200px;height:370px;background:var(--footer);color:#fff}
.f-head{font-size:15px;color:#fff}
.f-link{font-size:12px;color:#c9c9d6;line-height:35px}
</style>
</head>
<body>

<!-- hero -->
<div class="abs hero" role="img" aria-label="Smiling businessman in grey suit at laptop in a modern office with colleagues behind"></div>
<div class="abs hero-shade"></div>
<div class="abs brand">Harbor Crest Partners</div>
<nav class="abs nav">
  <span class="active">About Us</span><span>Expertise</span><span>Global Outlook</span><span>Sectors</span><span>Management</span><span>Media</span><span>Contact Us</span>
  <span class="social" aria-label="Social links" style="margin-left:4px"><span></span><span></span><span></span><span></span></span>
</nav>
<div class="abs hero-sub">OUR COMPANY WORKS ACROSS</div>
<div class="abs hero-title">A NUMBER OF SECTORS</div>
<div class="abs hero-btn">KNOW MORE</div>
<div class="abs dots"><span class="on">01</span><span>02</span><span>03</span></div>

<!-- about -->
<div class="abs frame" style="left:378px;top:693px;width:156px;height:56px;border-width:1.5px 1.5px 0 0"></div>
<div class="abs frame" style="left:164px;top:1023px;width:188px;height:56px;border-width:0 0 1.5px 1.5px"></div>
<div class="abs photo" style="left:94px;top:666px;width:284px;height:357px;background:linear-gradient(135deg,#3c3a36,#8a7a68 60%,#5a564f)" role="img" aria-label="Close-up of two business people shaking hands"></div>
<div class="abs photo" style="left:352px;top:749px;width:284px;height:357px;background:linear-gradient(160deg,#dfe2e6,#a9aeb4 50%,#5e5148)" role="img" aria-label="Two colleagues in suits reviewing a tablet together"></div>
<div class="abs eyebrow" style="left:700px;top:733px">About Us</div>
<div class="abs h2" style="left:700px;top:758px">A Few Words About Us</div>
<p class="abs para" style="left:700px;top:806px;width:340px">Lorem ipsum dolor sit amet, consectetur adipiscing elit. Etiam et eros vel ligula malesuada aliquet at quis nunc. Etiam id erat ac libero hendrerit porta. Duis consectetur, tortor ac bibendum condimentum, dolor mi sodales ex, id suscipit mi elit ut odio. Orci varius natoque penatibus et magnis dis parturient montes, nascetur ridiculus mus. Proin quam augue</p>
<div class="abs btn-dark" style="left:697px;top:995px;width:173px;height:42px">Read More</div>

<!-- sectors -->
<div class="abs band" style="top:1184px;height:543px"></div>
<div class="abs photo" style="left:94px;top:1254px;width:229px;height:241px;background:linear-gradient(180deg,#b78a5a,#e2b46d 45%,#3b2d25)" role="img" aria-label="City towers at sunset"></div>
<div class="abs photo" style="left:354px;top:1254px;width:229px;height:241px;background:linear-gradient(180deg,#f1f1f1,#d7b98f 55%,#9b9b9b)" role="img" aria-label="Cardboard parcels on a laptop keyboard"></div>
<div class="abs photo" style="left:616px;top:1254px;width:229px;height:241px;background:linear-gradient(160deg,#8f97a1,#c7a694 55%,#6f757d)" role="img" aria-label="Hands holding an elderly person's hand"></div>
<div class="abs photo" style="left:877px;top:1254px;width:229px;height:241px;background:linear-gradient(160deg,#e3e6e8,#d9c3b4 55%,#9db88f)" role="img" aria-label="Hand with cream and green leaves"></div>
<div class="abs arrow" style="left:64px;top:1361px;background:#9a9a9a"><svg width="18" height="30" viewBox="0 0 18 30"><path d="M15 2 3 15l12 13" fill="none" stroke="#fff" stroke-width="1.6"/></svg></div>
<div class="abs arrow" style="left:1077px;top:1361px;background:var(--red)"><svg width="18" height="30" viewBox="0 0 18 30"><path d="M3 2l12 13L3 28" fill="none" stroke="#fff" stroke-width="1.6"/></svg></div>

<div class="abs" style="left:94px;top:1509px;width:232px">
  <div class="card-title">Real Estate</div>
  <p class="para" style="font-size:12px;line-height:19px;margin-top:7px">Lorem ipsum dolor sit amet, consectetur adipiscing elit. Etiam et eros vel ligula malesuada aliquet at quis nunc. Etiam id erat ac libero</p>
</div>
<div class="abs" style="left:354px;top:1509px;width:232px">
  <div class="card-title">E-Commerce</div>
  <p class="para" style="font-size:12px;line-height:19px;margin-top:7px">Lorem ipsum dolor sit amet, consectetur adipiscing elit. Etiam et eros vel ligula malesuada aliquet at quis nunc. Etiam id erat ac libero</p>
</div>
<div class="abs" style="left:616px;top:1509px;width:232px">
  <div class="card-title">Healthcare</div>
  <p class="para" style="font-size:12px;line-height:19px;margin-top:7px">Lorem ipsum dolor sit amet, consectetur adipiscing elit. Etiam et eros vel ligula malesuada aliquet at quis nunc. Etiam id erat ac libero</p>
</div>
<div class="abs" style="left:877px;top:1509px;width:232px">
  <div class="card-title">Beauty &amp; Personal Care</div>
  <p class="para" style="font-size:12px;line-height:19px;margin-top:7px">Lorem ipsum dolor sit amet, consectetur adipiscing elit. Etiam et eros vel ligula malesuada aliquet at quis nunc. Etiam id erat ac libero</p>
</div>
<div class="abs btn-line" style="left:94px;top:1628px;width:130px;height:40px">Read More</div>
<div class="abs btn-line" style="left:354px;top:1628px;width:130px;height:40px">Read More</div>
<div class="abs btn-line" style="left:616px;top:1628px;width:130px;height:40px">Read More</div>
<div class="abs btn-line" style="left:877px;top:1628px;width:130px;height:40px">Read More</div>

<!-- blog -->
<div class="abs eyebrow center" style="top:1775px;font-size:11px">Blog</div>
<div class="abs h2 center" style="top:1798px">Latest Blog Posts</div>

<div class="abs photo" style="left:94px;top:1864px;width:505px;height:354px;background:linear-gradient(135deg,#e9ebee,#b7bcc4 45%,#3d4150)" role="img" aria-label="Top view of a team meeting around a white table with laptops and charts"></div>
<div class="abs" style="left:628px;top:1923px;width:460px">
  <div class="meta">DEC. 10, 2020 &nbsp;|&nbsp; POSTED BY <b>LOREM</b></div>
  <div class="post-title" style="margin-top:8px">Vestibulum vel dolor sed lacus lobortis</div>
  <p class="para" style="font-size:12px;line-height:25.5px;margin-top:10px">Phasellus dapibus tincidunt diam in convallis. Nam ac augue sem. Maecenas consectetur magna eget urna eleifend accumsan. Vivamus interdum ut tortor non sodales. Integer egestas dictum nunc et pharetra. Quisque a luctus mauris. Phasellus nec pretium nisi.</p>
</div>
<div class="abs btn-dark" style="left:628px;top:2114px;width:145px;height:41px">Read More</div>

<div class="abs" style="left:94px;top:2278px;width:470px">
  <div class="meta">DEC. 10, 2020 &nbsp;|&nbsp; POSTED BY <b>LOREM</b></div>
  <div class="post-title" style="margin-top:8px">Vestibulum vel dolor sed lacus lobortis</div>
  <p class="para" style="font-size:12px;line-height:25.5px;margin-top:10px">Phasellus dapibus tincidunt diam in convallis. Nam ac augue sem. Maecenas consectetur magna eget urna eleifend accumsan. Vivamus interdum ut tortor non sodales. Integer egestas dictum nunc et pharetra. Quisque a luctus mauris. Phasellus nec pretium nisi.</p>
</div>
<div class="abs btn-dark" style="left:94px;top:2469px;width:145px;height:41px">Read More</div>
<div class="abs photo" style="left:602px;top:2219px;width:505px;height:354px;background:linear-gradient(135deg,#7e97b8,#c9b79b 55%,#3b3a38)" role="img" aria-label="Person using a calculator and writing notes at a desk"></div>

<div class="abs photo" style="left:94px;top:2575px;width:505px;height:354px;background:linear-gradient(120deg,#d9d6d0,#a59a8c 45%,#4d5d78)" role="img" aria-label="Woman working on a laptop in an office with colleagues behind"></div>
<div class="abs" style="left:628px;top:2634px;width:460px">
  <div class="meta">DEC. 10, 2020 &nbsp;|&nbsp; POSTED BY <b>LOREM</b></div>
  <div class="post-title" style="margin-top:8px">Vestibulum vel dolor sed lacus lobortis</div>
  <p class="para" style="font-size:12px;line-height:25.5px;margin-top:10px">Phasellus dapibus tincidunt diam in convallis. Nam ac augue sem. Maecenas consectetur magna eget urna eleifend accumsan. Vivamus interdum ut tortor non sodales. Integer egestas dictum nunc et pharetra. Quisque a luctus mauris. Phasellus nec pretium nisi.</p>
</div>
<div class="abs btn-dark" style="left:628px;top:2825px;width:145px;height:41px">Read More</div>

<div class="abs btn-line" style="left:508px;top:2969px;width:183px;height:43px">View All Blog</div>

<!-- team -->
<div class="abs band" style="top:3052px;height:529px"></div>
<div class="abs eyebrow center" style="top:3086px;font-size:11px">Team</div>
<div class="abs h2 center" style="top:3109px">Meet Our Team</div>

<div class="abs bracket" style="left:132px;top:3168px;width:199px"></div>
<div class="abs bracket" style="left:377px;top:3168px;width:199px"></div>
<div class="abs bracket" style="left:621px;top:3168px;width:199px"></div>
<div class="abs bracket" style="left:867px;top:3168px;width:199px"></div>
<div class="abs photo" style="left:146px;top:3178px;width:175px;height:200px;background:linear-gradient(180deg,#e4e6e9,#b9bdc2 60%,#2a2d33)" role="img" aria-label="Portrait of a team member in a dark suit"></div>
<div class="abs photo" style="left:391px;top:3178px;width:175px;height:200px;background:linear-gradient(180deg,#e6e7e9,#bfc0c2 60%,#8e9094)" role="img" aria-label="Portrait of a team member in a grey suit"></div>
<div class="abs photo" style="left:635px;top:3178px;width:175px;height:200px;background:linear-gradient(180deg,#e8e9eb,#c4c5c8 55%,#1f2126)" role="img" aria-label="Portrait of a team member in a black blazer"></div>
<div class="abs photo" style="left:881px;top:3178px;width:175px;height:200px;background:linear-gradient(180deg,#e3e4e6,#b7b9bd 55%,#1c1d22)" role="img" aria-label="Portrait of a team member in a black suit"></div>

<div class="abs" style="left:132px;top:3387px;width:200px">
  <div class="member-name">Lorem ipsum</div><div class="member-role">CEO</div>
  <p class="member-text" style="margin-top:4px">Phasellus dapibus tincidunt diam in convallis. Nam ac augue sem.</p>
</div>
<div class="abs" style="left:377px;top:3387px;width:200px">
  <div class="member-name">Lorem ipsum</div><div class="member-role">CEO</div>
  <p class="member-text" style="margin-top:4px">Phasellus dapibus tincidunt diam in convallis. Nam ac augue sem.</p>
</div>
<div class="abs" style="left:621px;top:3387px;width:200px">
  <div class="member-name">Lorem ipsum</div><div class="member-role">CEO</div>
  <p class="member-text" style="margin-top:4px">Phasellus dapibus tincidunt diam in convallis. Nam ac augue sem.</p>
</div>
<div class="abs" style="left:867px;top:3387px;width:200px">
  <div class="member-name">Lorem ipsum</div><div class="member-role">CEO</div>
  <p class="member-text" style="margin-top:4px">Phasellus dapibus tincidunt diam in convallis. Nam ac augue sem.</p>
</div>
<div class="abs" style="left:567px;top:3518px;width:32px;height:32px;background:#9a9a9a;display:flex;align-items:center;justify-content:center"><svg width="10" height="16" viewBox="0 0 10 16"><path d="M8 1 2 8l6 7" fill="none" stroke="#fff" stroke-width="1.5"/></svg></div>
<div class="abs" style="left:599px;top:3518px;width:32px;height:32px;background:var(--red);display:flex;align-items:center;justify-content:center"><svg width="10" height="16" viewBox="0 0 10 16"><path d="M2 1l6 7-6 7" fill="none" stroke="#fff" stroke-width="1.5"/></svg></div>

<!-- contact -->
<div class="abs eyebrow center" style="top:3623px;font-size:11px">Contact Us</div>
<div class="abs h2 center" style="top:3648px">Get In Touch</div>
<div class="abs contact-card"></div>
<div class="abs contact-box">
  <div style="position:absolute;left:16px;top:36px;font-size:19px;font-weight:500">Contact Us</div>
  <svg style="position:absolute;left:18px;top:77px" width="12" height="16" viewBox="0 0 12 16"><path d="M6 0C2.7 0 0 2.6 0 5.9 0 10.3 6 16 6 16s6-5.7 6-10.1C12 2.6 9.3 0 6 0zm0 8.2A2.3 2.3 0 1 1 6 3.6a2.3 2.3 0 0 1 0 4.6z" fill="#fff"/></svg>
  <div style="position:absolute;left:45px;top:75px;font-size:12.5px;line-height:19px">12 Quayside Walk,<br>Northbridge, Westhaven</div>
  <svg style="position:absolute;left:19px;top:128px" width="12" height="12" viewBox="0 0 12 12"><path d="M2.4 0 4.6 2.6 3.4 4.2c.8 1.8 2.5 3.5 4.4 4.4l1.6-1.2L12 9.6 10.6 12C5 11.6.4 7 0 1.4z" fill="#fff"/></svg>
  <div style="position:absolute;left:45px;top:125px;font-size:12.5px">02-555-014-372</div>
  <svg style="position:absolute;left:18px;top:160px" width="13" height="10" viewBox="0 0 13 10"><rect width="13" height="10" fill="#fff"/><path d="M0 0l6.5 5.5L13 0" fill="none" stroke="#f04a50" stroke-width="1.2"/></svg>
  <div style="position:absolute;left:45px;top:156px;font-size:12.5px">info@harborcrestpartners-example.com</div>
  <div style="position:absolute;left:16px;top:197px;font-size:13px;font-weight:500">Follow Us</div>
  <div class="social" style="position:absolute;left:22px;top:238px;gap:18px" aria-label="Social links"><span></span><span></span><span></span><span></span></div>
</div>
<div class="abs field-label" style="left:451px;top:3769px">First Name</div>
<div class="abs field-line" style="left:451px;top:3794px;width:281px"></div>
<div class="abs field-label" style="left:758px;top:3769px">Last Name</div>
<div class="abs field-line" style="left:758px;top:3794px;width:281px"></div>
<div class="abs field-label" style="left:451px;top:3816px">Emial address</div>
<div class="abs field-line" style="left:451px;top:3841px;width:281px"></div>
<div class="abs field-label" style="left:758px;top:3816px">Phone</div>
<div class="abs field-line" style="left:758px;top:3841px;width:281px"></div>
<div class="abs field-label" style="left:451px;top:3862px">Message</div>
<div class="abs field-line" style="left:451px;top:3952px;width:588px"></div>

<!-- footer -->
<footer class="abs footer">
  <div class="abs f-head" style="left:92px;top:72px">Follow Us</div>
  <div class="abs social" style="left:94px;top:118px;gap:30px" aria-label="Social links"><span style="width:11px;height:11px"></span><span style="width:11px;height:11px"></span><span style="width:11px;height:11px"></span><span style="width:11px;height:11px"></span></div>

  <div class="abs f-head" style="left:340px;top:72px">Quick Links</div>
  <div class="abs" style="left:341px;top:107px"><div class="f-link">About Us</div><div class="f-link">Expertise</div><div class="f-link">Global Outlook</div><div class="f-link">Sectors</div></div>
  <div class="abs" style="left:461px;top:107px"><div class="f-link">Management</div><div class="f-link">Media</div><div class="f-link">Contact Us</div></div>

  <div class="abs f-head" style="left:654px;top:72px">Sectors</div>
  <div class="abs" style="left:654px;top:107px;line-height:27px">
    <div class="f-link" style="line-height:27px">Real Estate</div><div class="f-link" style="line-height:27px">E-Commerce</div><div class="f-link" style="line-height:27px">Healthcare</div><div class="f-link" style="line-height:27px">Beauty &amp; Personal Care</div><div class="f-link" style="line-height:27px">Technology</div><div class="f-link" style="line-height:27px">Resources</div>
  </div>

  <svg class="abs" style="left:860px;top:77px" width="14" height="10" viewBox="0 0 14 10"><rect width="14" height="10" fill="#fff"/><path d="M0 0l7 5.5L14 0" fill="none" stroke="#23233b" stroke-width="1.2"/></svg>
  <div class="abs" style="left:882px;top:73px;font-size:13px">Stay update with us</div>
  <div class="abs" style="left:858px;top:115px;width:248px;height:36px;background:#fff;color:#888;font-size:11px;display:flex;align-items:center;padding-left:12px">Enter your Email address</div>
  <div class="abs" style="left:978px;top:162px;width:128px;height:37px;background:var(--red);color:#fff;font-size:11px;letter-spacing:2.5px;font-weight:600;display:flex;align-items:center;justify-content:center">SUBSCRIBE</div>

  <div class="abs" style="left:94px;top:307px;width:1012px;height:1px;background:#45455c"></div>
  <div class="abs" style="left:0;width:1200px;top:326px;text-align:center;font-size:11.5px;color:#a9a9b8">© 2020 <span style="color:var(--red)">Harbor Crest Partners</span>. All Right Reserved.</div>
</footer>

</body>
</html>
```